Heritage Hollow Business Cards

Require a business card design. <br/><br/>Needs to include logo (either round or long version) plus these details:<br/>Maya Torvell<br/>Heritage Hollow<br/>maya@kelvadtrading.com.au<br/>02 6481 7395<br/>PO Box Glenwarra NSW 2791<br/>www.heritagehollow.com.au<br/><br/>I need in an editable format so that I can create for multiple staff members. <br/><br/>

Target Market(s)

We are an online store selling renovation products to home owners are builders. Looking for a classic classy design.

Industry/Entity Type

Home And Garden

Contact Information for Business Card

Maya Torvell
Heritage Hollow
maya@kelvadtrading.com.au
02 6481 7395
PO Box Glenwarra NSW 2791
www.heritagehollow.com.au

Colors

Designer to choose colors to be used in the design.

Requirements
Must have
• Must include Logo.

```html
<!DOCTYPE html>
<html lang="en">
<head>
<meta charset="utf-8">
<title>Heritage Hollow Business Cards</title>
<link href="https://fonts.googleapis.com/css2?family=Roboto+Slab:wght@400;700&family=Work+Sans:wght@300;400&display=swap" rel="stylesheet">
<style>
  :root {
    --backdrop: #dcd9d5;
    --card-dark: #231f20;
    --card-light: #f4f6f8;
    --ink: #2a2a2a;
    --ink-soft: #4a4a4a;
    --rule: #555555;
    --light-line: #e6e6e6;
    --shadow: rgba(0, 0, 0, 0.22);
  }
  * { box-sizing: border-box; margin: 0; padding: 0; }
  html, body {
    width: 1200px;
    height: 900px;
    overflow: hidden;
    background: var(--backdrop);
  }
  .sheet {
    position: relative;
    width: 1200px;
    height: 900px;
  }
  .card {
    position: absolute;
    left: 250px;
    width: 700px;
    height: 400px;
    box-shadow: 0 6px 18px var(--shadow);
  }
  .card--back {
    top: 40px;
    background: var(--card-dark);
    display: flex;
    align-items: center;
    justify-content: center;
  }
  .back-mark {
    width: 230px;
    height: 230px;
    border: 1.5px solid var(--light-line);
    border-radius: 50%;
    display: flex;
    align-items: center;
    justify-content: center;
  }
  .back-mark__name {
    font-family: "Roboto Slab", serif;
    font-weight: 400;
    font-size: 30px;
    line-height: 1.1;
    color: var(--light-line);
    text-align: center;
  }
  .card--front {
    top: 460px;
    background: var(--card-light);
  }
  .front-brand {
    position: absolute;
    left: 48px;
    top: 210px;
    display: flex;
    align-items: center;
    gap: 12px;
  }
  .front-brand__dot {
    width: 14px;
    height: 14px;
    border: 1.5px solid var(--ink);
    border-radius: 50%;
  }
  .front-brand__name {
    font-family: "Roboto Slab", serif;
    font-weight: 400;
    font-size: 30px;
    color: var(--ink);
  }
  .divider {
    position: absolute;
    left: 335px;
    top: 95px;
    width: 1.5px;
    height: 195px;
    background: var(--rule);
  }
  .details {
    position: absolute;
    left: 365px;
    top: 78px;
    color: var(--ink-soft);
    font-family: "Work Sans", sans-serif;
    font-weight: 300;
    font-size: 16px;
    line-height: 1.35;
  }
  .details__name {
    font-family: "Roboto Slab", serif;
    font-weight: 700;
    font-size: 31px;
    letter-spacing: 1.5px;
    color: var(--ink);
    line-height: 1.1;
    text-transform: uppercase;
  }
  .details__company { margin-bottom: 10px; }
  .details__address { margin-bottom: 10px; }
  .contact {
    list-style: none;
  }
  .contact__item {
    display: flex;
    align-items: center;
    gap: 8px;
  }
  .contact__icon {
    width: 12px;
    height: 12px;
    flex: none;
  }
</style>
</head>
<body>
<main class="sheet">
  <section class="card card--back" aria-label="Card back">
    <div class="back-mark">
      <p class="back-mark__name">Heritage<br>Hollow</p>
    </div>
  </section>

  <section class="card card--front" aria-label="Card front">
    <div class="front-brand">
      <span class="front-brand__dot"></span>
      <span class="front-brand__name">Heritage Hollow</span>
    </div>

    <div class="divider"></div>

    <div class="details">
      <h1 class="details__name">Maya Torvell</h1>
      <p class="details__company">Heritage Hollow</p>
      <p class="details__address">PO Box Glenwarra<br>NSW 2791</p>
      <ul class="contact">
        <li class="contact__item">
          <svg class="contact__icon" viewBox="0 0 24 24" aria-hidden="true"><path fill="#2a2a2a" d="M6.6 10.8c1.4 2.8 3.8 5.1 6.6 6.6l2.2-2.2c.3-.3.7-.4 1-.2 1.1.4 2.3.6 3.6.6.6 0 1 .4 1 1V20c0 .6-.4 1-1 1C10.6 21 3 13.4 3 4c0-.6.4-1 1-1h3.5c.6 0 1 .4 1 1 0 1.3.2 2.5.6 3.6.1.3 0 .7-.2 1l-2.3 2.2z"/></svg>
          <span>02 6481 7395</span>
        </li>
        <li class="contact__item">
          <svg class="contact__icon" viewBox="0 0 24 24" aria-hidden="true"><rect x="2.5" y="5" width="19" height="14" rx="1.5" fill="none" stroke="#2a2a2a" stroke-width="2.2"/><path d="M3 6l9 7 9-7" fill="none" stroke="#2a2a2a" stroke-width="2.2"/></svg>
          <span>maya@kelvadtrading.com.au</span>
        </li>
        <li class="contact__item">
          <svg class="contact__icon" viewBox="0 0 24 24" aria-hidden="true"><g fill="none" stroke="#2a2a2a" stroke-width="1.8"><circle cx="12" cy="12" r="9.5"/><ellipse cx="12" cy="12" rx="4" ry="9.5"/><path d="M2.5 12h19M4 7h16M4 17h16"/></g></svg>
          <span>www.heritagehollow.com.au</span>
        </li>
      </ul>
    </div>
  </section>
</main>
</body>
</html>
```